The Copper Kite Website Redesign

I want a new design and website for www.thecopperkitebrookvale.com where part of the home page includes our daily specials from our POS Toast to be pulled from API. I have included photos and links to give you a better feel for the style of our restaurant.

Coding

Coded - Design and coding required

```html
<!DOCTYPE html>
<html lang="en">
<head>
<meta charset="utf-8">
<title>The Copper Kite — A Finer Diner</title>
<link href="https://fonts.googleapis.com/css2?family=Ribeye&family=Roboto:wght@400;500;700&display=swap" rel="stylesheet">
<style>
:root{
  --red:#e02a2b;
  --red-dark:#b81c1d;
  --ink:#222222;
  --body:#555555;
  --line:#cfcfcf;
  --cream:#f9ede3;
  --white:#ffffff;
  --grey-btn:#5a5a5a;
}
*{box-sizing:border-box;margin:0;padding:0}
html,body{width:1200px;height:3880px;overflow:hidden;background:var(--white)}
body{position:relative;font-family:'Roboto',sans-serif;color:var(--ink)}
.abs{position:absolute}
.display{font-family:'Ribeye',serif;font-weight:400;white-space:nowrap}
.btn{position:absolute;display:flex;align-items:center;justify-content:center;border-radius:30px;background:var(--red);color:var(--white);font-weight:700;font-size:14px;text-transform:uppercase;letter-spacing:.2px}

/* header */
.topline{left:0;top:0;width:1200px;height:4px;background:var(--red)}
.hero{left:0;top:105px;width:1200px;height:556px;background:radial-gradient(ellipse at 82% 40%,#c98a3f 0%,#8a4a2a 22%,#2c2a2a 48%,#1f1f21 100%)}
.hero-cut{left:0;top:560px}
.logo-tab{left:0;top:0;width:400px;height:140px}
.brand{left:140px;top:38px;font-size:33px;font-weight:700;color:var(--red);display:flex;align-items:center;gap:10px}
.brand .dot{width:16px;height:16px;border-radius:50%;background:var(--red)}
.brand-sub{left:168px;top:84px;font-size:15px;color:var(--ink);font-style:italic}
.contact-top{top:18px;display:flex;align-items:center;gap:8px}
.phone-top{left:680px;font-size:20px;font-weight:500;color:var(--red)}
.addr-top{left:868px;font-size:12.5px;line-height:18px;color:var(--body)}
.nav{left:527px;top:68px;display:flex;gap:26px;align-items:center;font-size:15px;font-weight:500;color:var(--ink)}
.nav .on{background:var(--red);color:var(--white);border-radius:16px;padding:5px 11px}
.hero-title{left:143px;top:248px;font-size:39px;line-height:56px;color:var(--white)}
.hero-title .hl{color:var(--red)}
.slide-arrow{width:42px;height:42px;border-radius:50%;border:2px solid var(--white);display:flex;align-items:center;justify-content:center}

/* specials */
.sec-title{font-size:37px;color:var(--red);text-align:center;width:1200px;left:0}
.card{background:var(--white);border:1px solid var(--line);text-align:center}
.card h3{font-size:18px;font-weight:500;color:var(--ink)}
.card .price{font-size:18px;font-weight:500;color:var(--red);margin-top:10px}
.card p{font-size:12.5px;line-height:21px;color:var(--body);margin:8px auto 0;width:246px}
.photo-circle{border-radius:50%}
.circle-arrow{width:44px;height:44px;border-radius:50%;border:1.5px solid #888;background:var(--white);display:flex;align-items:center;justify-content:center}

/* retail */
.retail-title{left:601px;top:1462px;font-size:38px;color:var(--white)}
.retail-sub{left:601px;top:1518px;font-size:25px;color:var(--white)}
.retail-text{left:601px;top:1566px;width:454px;font-size:14.5px;line-height:24px;color:var(--white);text-align:justify}

/* faq */
.faq-title{left:143px;top:2038px;font-size:34px;color:var(--red)}
.faq{left:152px;top:2122px;width:497px}
.faq-row{height:66px;border-bottom:1.5px solid #b5b5b5;display:flex;align-items:center;justify-content:space-between;font-size:17px;color:var(--ink)}
.faq-ico{width:26px;height:26px;border-radius:50%;background:var(--grey-btn);color:var(--white);display:flex;align-items:center;justify-content:center;font-size:17px;line-height:1}
.faq-ico.open{background:var(--red)}
.faq-answer{left:159px;top:2468px;width:460px;font-size:14px;line-height:24px;color:var(--body)}

/* press */
.press-card{background:var(--white);border-radius:60px;text-align:center;box-shadow:0 8px 18px rgba(0,0,0,.06)}
.press-card h3{font-size:20px;font-weight:500;line-height:26px;color:var(--ink);margin:38px auto 0;width:300px}
.press-card p{font-size:13px;line-height:23px;color:var(--body);margin:14px auto 0;width:300px}

/* contact */
.contact-item{left:236px;display:flex;align-items:flex-start;gap:14px;font-size:13.5px;line-height:22px;color:var(--body)}
.c-ico{width:26px;height:26px;border-radius:50%;border:1.5px solid var(--red);display:flex;align-items:center;justify-content:center;flex:none}
.field{border:1.5px solid #8a8a8a;background:var(--white);font-size:13px;color:#777;padding:12px 22px}
.footer{left:116px;top:3810px;width:953px;height:70px;background:var(--red);border-radius:60px 60px 0 0}
.footer-in{left:132px;top:3822px;width:921px;height:58px;background:#2a2a2a;border-radius:50px 50px 0 0;display:flex;align-items:center;justify-content:space-between;padding:0 56px 0 46px;color:var(--white);font-size:13px}
.soc{display:flex;gap:6px}
.soc span{width:24px;height:24px;border-radius:50%;border:2px solid var(--white)}
.soc span.mid{background:var(--red)}
</style>
</head>
<body>

<div class="abs topline"></div>

<!-- hero -->
<div class="abs hero" role="img" aria-label="Dark stone table with a plate of smashed garlic fried potatoes topped with ham, cilantro and salsa"></div>
<svg class="abs hero-cut" width="1200" height="101" viewBox="0 0 1200 101" aria-hidden="true">
  <path d="M540 101 C560 60 590 35 650 35 H1200 V101 Z" fill="#fff"/>
</svg>
<svg class="abs logo-tab" viewBox="0 0 400 140" aria-hidden="true">
  <path d="M0 0 H400 V105 H395 C380 105 370 138 330 138 H0 Z" fill="#fff"/>
</svg>
<div class="abs brand"><span class="dot"></span>The Copper Kite</div>
<div class="abs brand-sub">a finer diner</div>

<div class="abs contact-top phone-top">
  <svg width="24" height="24" viewBox="0 0 24 24"><circle cx="12" cy="12" r="12" fill="#222"/><path d="M8 6.5l2 2-1.2 1.6c.8 1.7 2 2.9 3.6 3.6l1.6-1.2 2 2-1.2 1.8c-4 0-8.6-4.6-8.6-8.6z" fill="#fff"/></svg>
  (313) 555 0142
</div>
<div class="abs contact-top addr-top">
  <svg width="24" height="24" viewBox="0 0 24 24"><circle cx="12" cy="12" r="11" fill="none" stroke="#e02a2b" stroke-width="1.5"/><path d="M12 6a4 4 0 0 1 4 4c0 3-4 8-4 8s-4-5-4-8a4 4 0 0 1 4-4z" fill="#222"/><circle cx="12" cy="10" r="1.5" fill="#fff"/></svg>
  <div>4180 Harbor Avenue<br>Brookvale,Michigan 48731</div>
</div>
<nav class="abs nav">
  <span class="on">HOME</span><span>ABOUT US</span><span>MENU</span><span>RETAIL</span><span>PRESS</span><span>CONTACT US</span>
</nav>

<h1 class="abs display hero-title">Comes With Toast &amp;<br><span class="hl">Smashed Garlic Fried</span><br>Potatoes when Logical</h1>
<div class="btn" style="left:143px;top:449px;width:158px;height:54px">Get Started</div>
<div class="abs slide-arrow" style="left:943px;top:574px;background:var(--red)"><svg width="20" height="14" viewBox="0 0 20 14"><path d="M19 7H2M8 1L2 7l6 6" fill="none" stroke="#fff" stroke-width="2"/></svg></div>
<div class="abs slide-arrow" style="left:988px;top:574px;background:#555"><svg width="20" height="14" viewBox="0 0 20 14"><path d="M1 7h17M12 1l6 6-6 6" fill="none" stroke="#fff" stroke-width="2"/></svg></div>

<!-- specials -->
<h2 class="abs display sec-title" style="top:742px">Our Specials</h2>

<div class="abs circle-arrow" style="left:67px;top:1056px"><svg width="12" height="20" viewBox="0 0 12 20"><path d="M10 2L2 10l8 8" fill="none" stroke="#555" stroke-width="2"/></svg></div>
<div class="abs circle-arrow" style="left:1088px;top:1056px"><svg width="12" height="20" viewBox="0 0 12 20"><path d="M2 2l8 8-8 8" fill="none" stroke="#555" stroke-width="2"/></svg></div>

<div class="abs card" style="left:149px;top:875px;width:286px;height:407px;border-radius:143px 143px 0 0">
  <div class="abs photo-circle" style="left:40px;top:16px;width:206px;height:206px;background:radial-gradient(circle,#8a4a25,#3b2418)" role="img" aria-label="Green eggs and ham with seared ham pieces"></div>
  <div style="margin-top:240px"><h3>Green Eggs and Ham</h3><div class="price">$13.95</div><p>Poblano Pesto and Jack Cheese Rumbled with Eggs Sidled by Seared City Ham</p></div>
</div>
<div class="btn" style="left:228px;top:1261px;width:128px;height:44px">Order Now</div>

<div class="abs card" style="left:458px;top:875px;width:284px;height:407px;border:1.5px solid var(--red);border-radius:0 0 142px 142px;box-shadow:0 10px 24px rgba(0,0,0,.08)">
  <div style="margin-top:44px"><h3>Veggie Rumble</h3><div class="price">$12.95</div><p>Red Pepper, Carrots, Mushrooms, Peas, Spinach and Provolone. Choose Eggs or Tofu</p></div>
  <div class="abs photo-circle" style="left:40px;top:185px;width:204px;height:204px;background:radial-gradient(circle,#c9a85a,#5b4a2a)" role="img" aria-label="Veggie rumble scramble with spinach and mushrooms"></div>
</div>
<div class="btn" style="left:537px;top:852px;width:128px;height:44px">Order Now</div>

<div class="abs card" style="left:765px;top:875px;width:285px;height:407px;border-radius:143px 143px 0 0">
  <div class="abs photo-circle" style="left:40px;top:16px;width:206px;height:206px;background:radial-gradient(circle,#5e9a3a,#c7c2b8 65%,#9a2a25)" role="img" aria-label="Huevos rancheros with jalapeño and pico de gallo"></div>
  <div style="margin-top:240px"><h3>Huevos Rancheros</h3><div class="price">$13.95</div><p>Two Eggs Any Style, Crispy Flour Tortilla, Black Beans, Jack Cheese, Jalapeños, Pico de Gallo &amp; Sour Cream</p></div>
</div>
<div class="btn" style="left:843px;top:1261px;width:128px;height:44px">Order Now</div>

<!-- retail -->
<svg class="abs" style="left:0;top:1370px" width="1200" height="575" viewBox="0 0 1200 575" aria-hidden="true">
  <path d="M0 50 H300 C350 50 355 19 410 19 H1200 V513 H650 C590 513 575 575 540 575 H0 Z" fill="#e02a2b"/>
</svg>
<div class="abs" style="left:90px;top:1483px;width:460px;height:392px;border-radius:58% 42% 40% 60% / 55% 45% 55% 45%;background:linear-gradient(110deg,#6a3fa0 0%,#8bd040 38%,#c2562a 55%,#3a9ad8 80%,#1a2a5a 100%)" role="img" aria-label="Three bottles of Zing hot sauce in purple, green and blue labels"></div>
<h2 class="abs display retail-title">Retail</h2>
<div class="abs retail-sub">Zing Sauces</div>
<p class="abs retail-text">Sed ut perspiciatis unde omnis iste natus error sit voluptatem accusantium doloremque laudantium, totam rem aperiam, eaque ipsa quae ab illo inventore veritatis et quasi architecto beatae vitae dicta sunt explicabo. Nemo enim ipsam voluptatem quia voluptas sit aspernatur aut odit aut fugit, sed quia consequuntur magni dolores eos qui ratione voluptatem sequi nesciunt. Neque porro quisquam est, qui dolorem ipsum quia dolor sit amet, consectetur, adipisci velit</p>
<div class="btn" style="left:602px;top:1762px;width:146px;height:48px;background:var(--white);color:var(--red)">Read More</div>

<!-- faq -->
<div class="abs" style="left:738px;top:1947px;width:462px;height:591px;border-radius:45% 55% 0 60% / 30% 40% 0 70%;background:linear-gradient(160deg,#3a4a7a 0%,#c24a4a 35%,#8a5a30 60%,#c98f4a 80%,#3a2a20 100%)" role="img" aria-label="Waffles with berries and a small syrup pitcher on a diner counter"></div>
<h2 class="abs display faq-title">What else is there to know?</h2>
<div class="abs faq">
  <div class="faq-row">Do you take Reservations?<span class="faq-ico">+</span></div>
  <div class="faq-row">Do you do carry-out?<span class="faq-ico">+</span></div>
  <div class="faq-row">Do you deliver?<span class="faq-ico">+</span></div>
  <div class="faq-row">How large is your restaurant?<span class="faq-ico">+</span></div>
  <div class="faq-row">Why didn't you answer my question?<span class="faq-ico open">-</span></div>
</div>
<p class="abs faq-answer">We didn't know you had one! Please email or with any questions not covered within the pages of this website.</p>

<!-- press -->
<svg class="abs" style="left:0;top:2600px" width="1200" height="783" viewBox="0 0 1200 783" aria-hidden="true">
  <path d="M0 30 H300 C350 30 355 0 410 0 H1200 V727 H650 C590 727 575 783 540 783 H0 Z" fill="#f9ede3"/>
</svg>
<h2 class="abs display sec-title" style="top:2705px">Press Releases</h2>
<div class="abs circle-arrow" style="left:67px;top:2900px"><svg width="12" height="20" viewBox="0 0 12 20"><path d="M10 2L2 10l8 8" fill="none" stroke="#555" stroke-width="2"/></svg></div>
<div class="abs circle-arrow" style="left:1088px;top:2900px"><svg width="12" height="20" viewBox="0 0 12 20"><path d="M2 2l8 8-8 8" fill="none" stroke="#555" stroke-width="2"/></svg></div>

<div class="abs" style="left:143px;top:2798px;width:434px;height:240px;border-radius:60px 60px 0 60px;background:linear-gradient(150deg,#b8485a,#e0c8b8 45%,#a83a30 80%)" role="img" aria-label="Plates of diner food on a red table"></div>
<div class="abs press-card" style="left:163px;top:2997px;width:396px;height:248px;border-bottom:3px solid var(--red);border-right:3px solid var(--red)">
  <h3>Don't swat it - Copper Kite is a 'finer diner'</h3>
  <p>BROOKVALE – Don't be put off by the name.The Copper Kite is a tongue-in-cheek reference to the more modest predecessor that filled the space</p>
</div>
<div class="btn" style="left:298px;top:3178px;width:127px;height:45px">Read More</div>

<div class="abs" style="left:622px;top:2798px;width:434px;height:240px;border-radius:60px 60px 60px 0;background:linear-gradient(90deg,#2a2a2a 0%,#3a3a30 30%,#e8d23a 45%,#f0dc40 80%,#c8b030 100%)" role="img" aria-label="Yellow diner storefront with a sign above the door"></div>
<div class="abs press-card" style="left:642px;top:2997px;width:394px;height:248px">
  <h3>Here's a 'Kite' we want flying</h3>
  <p>The neon sign above the door really does say "The Copper Kite" (and in smaller letters "a finer diner"). The menu proclaims that eggs come with toast and potatoes "when logical."</p>
</div>
<div class="btn" style="left:776px;top:3178px;width:127px;height:45px">Read More</div>

<!-- contact -->
<div class="abs" style="left:0;top:3383px;width:1200px;height:497px;background:linear-gradient(180deg,#ffffff 0%,#f4f0ee 45%,#e7dfd9 100%)" role="img" aria-label="Faint city skyline behind the contact area"></div>
<h2 class="abs display sec-title" style="top:3457px">Contact Us</h2>

<div class="abs contact-item" style="top:3551px"><span class="c-ico"><svg width="12" height="12" viewBox="0 0 12 12"><path d="M6 1a3 3 0 0 1 3 3c0 2.5-3 7-3 7S3 6.5 3 4a3 3 0 0 1 3-3z" fill="#e02a2b"/></svg></span><div>4180 Harbor Avenue<br>Brookvale, Michigan 48731</div></div>
<div class="abs contact-item" style="top:3603px"><span class="c-ico"><svg width="12" height="12" viewBox="0 0 12 12"><path d="M2 1.5l2 2-1 1.3c.7 1.5 1.8 2.6 3.2 3.2L7.5 7l2 2-1 1.5C5 10.5 1.5 7 1.5 3z" fill="#e02a2b"/></svg></span><div>Phone (313) 555-0187</div></div>
<div class="abs contact-item" style="top:3655px"><span class="c-ico"><svg width="12" height="10" viewBox="0 0 12 10"><rect x="1" y="1" width="10" height="8" fill="#e02a2b"/><path d="M1 1l5 4 5-4" fill="none" stroke="#fff"/></svg></span><div>eat@thecopperkitebrookvale.com</div></div>
<div class="abs contact-item" style="top:3710px"><span class="c-ico"><svg width="12" height="12" viewBox="0 0 12 12"><circle cx="6" cy="6" r="5" fill="none" stroke="#e02a2b" stroke-width="1.5"/><path d="M6 3v3h2" fill="none" stroke="#e02a2b" stroke-width="1.5"/></svg></span><div>Sat. - Sun. 8 a.m. - 3 p.m.</div></div>

<div class="abs field" style="left:545px;top:3551px;width:205px;height:44px">Enter Name</div>
<div class="abs field" style="left:763px;top:3551px;width:205px;height:44px">Enter Email</div>
<div class="abs field" style="left:545px;top:3607px;width:423px;height:77px">Message</div>
<div class="btn" style="left:547px;top:3700px;width:126px;height:45px">Submit</div>

<!-- footer -->
<div class="abs footer"></div>
<div class="abs footer-in">
  <span>© 2025 The Copper Kite.All rights reserved. Terms of Use &nbsp;&nbsp;|&nbsp;&nbsp; Privacy Policy</span>
  <span class="soc"><span></span><span class="mid"></span><span></span></span>
</div>

</body>
</html>
```